Business Card Design

We need a business card designed for our new company. Prefer a black card with white logo & writing.

Contact Information for Business Card

Ted Galloway, address: 7-4812 Fernhollow Road, Abbotsford, BC, V3K 8R2, Office Phone: 604-712-3390, Cell: 604-947-2164, Email: ted@resinworkshub.ca

Colors

Designer to choose only greyscale colors for use in the design.

```html
<!DOCTYPE html>
<html lang="en">
<head>
<meta charset="utf-8">
<title>Resin Works Hub — Business Card</title>
<link rel="stylesheet" href="https://fonts.googleapis.com/css2?family=Montserrat:wght@400;700;800&display=swap">
<style>
  :root {
    --backdrop: #2a2a2a;
    --card-black: #141414;
    --ink-white: #ffffff;
    --ink-soft: #e6e6e6;
    --disc-light: #5a5a5a;
    --disc-dark: #050505;
  }
  * { margin: 0; padding: 0; box-sizing: border-box; }
  html, body {
    width: 1200px; height: 900px; overflow: hidden;
    background: var(--backdrop);
    font-family: "Montserrat", sans-serif;
  }
  .canvas {
    position: relative; width: 1200px; height: 900px;
    display: flex; align-items: center; justify-content: center;
  }
  .business-card {
    position: relative; width: 1050px; height: 600px;
    background: var(--card-black);
    color: var(--ink-white);
    overflow: hidden;
    box-shadow: 0 20px 50px rgba(0,0,0,0.5);
  }
  .brand-name {
    position: absolute; left: 70px; top: 64px;
    font-weight: 800; font-size: 40px; line-height: 1;
    letter-spacing: 1px; text-transform: uppercase;
    display: flex; align-items: center; gap: 14px;
  }
  .brand-mark {
    width: 26px; height: 26px; border-radius: 50%;
    background: var(--ink-white);
  }
  .contact-block {
    position: absolute; left: 70px; top: 190px;
    font-size: 24px; font-weight: 400; line-height: 1.4;
    color: var(--ink-soft);
  }
  .address { margin-bottom: 26px; }
  .contact-line { display: flex; align-items: center; gap: 12px; }
  .contact-line svg { width: 22px; height: 22px; flex: none; }
  .person {
    position: absolute; right: 70px; top: 270px;
    display: flex; align-items: stretch; gap: 18px;
    text-align: right;
  }
  .person-name { font-weight: 700; font-size: 40px; line-height: 1.1; }
  .person-title { font-size: 24px; font-weight: 400; color: var(--ink-soft); margin-top: 6px; }
  .title-bar { width: 10px; background: var(--ink-white); }
  .feature-disc {
    position: absolute; left: 410px; top: 280px;
    width: 300px; height: 300px; border-radius: 50%;
    background: radial-gradient(circle at 50% 20%, var(--disc-light), #1a1a1a 60%, var(--disc-dark));
  }
</style>
</head>
<body>
<main class="canvas">
  <article class="business-card">
    <div class="brand-name"><span class="brand-mark"></span>Resin Works Hub</div>

    <section class="contact-block">
      <p class="address">7-4812 Fernhollow Road,<br>Abbotsford, BC, V3K 8R2</p>
      <p class="contact-line">
        <svg viewBox="0 0 24 24" aria-hidden="true"><path fill="#fff" d="M6.6 10.8a15 15 0 0 0 6.6 6.6l2.2-2.2a1 1 0 0 1 1-.25 11.4 11.4 0 0 0 3.6.57 1 1 0 0 1 1 1V20a1 1 0 0 1-1 1A17 17 0 0 1 3 4a1 1 0 0 1 1-1h3.5a1 1 0 0 1 1 1c0 1.25.2 2.45.57 3.57a1 1 0 0 1-.25 1z"/></svg>
        604-712-3390
      </p>
      <p class="contact-line">
        <svg viewBox="0 0 24 24" aria-hidden="true"><rect x="6" y="2" width="12" height="20" rx="2" fill="#fff"/><rect x="8" y="5" width="8" height="12" fill="#141414"/><circle cx="12" cy="19.5" r="1" fill="#141414"/></svg>
        604-947-2164
      </p>
      <p class="contact-line">
        <svg viewBox="0 0 24 24" aria-hidden="true"><rect x="2" y="5" width="20" height="14" rx="2" fill="#fff"/><path d="M3 6l9 7 9-7" fill="none" stroke="#141414" stroke-width="1.8"/></svg>
        ted@resinworkshub.ca
      </p>
    </section>

    <section class="person">
      <div>
        <p class="person-name">Ted Galloway</p>
        <p class="person-title">Owner/CEO</p>
      </div>
      <span class="title-bar"></span>
    </section>

    <div class="feature-disc" role="img" aria-label="Glossy black disc with the company emblem embossed"></div>
  </article>
</main>
</body>
</html>
```